Financial Advisor Resource Firm needs business card design

Need business card design for company in Omaha NE called Meridale Circle. We provide resources to financial advisors....workshop programs, retirement analysis, and insurance planning. I would like to see designs that use grays, greens, black, and white colors. The final design should communicate 'collaboration' and be simple yet attractive to financial planning clients. I will attached our logo and another picture of a puzzle piece coming together. I would like the incorporate the puzzle picture somehow, maybe on the back somehow, with color or just the gray scale....OR, the picture be the front of the card with 'Meridale' definition on it (see upload) and then company logo, employee name, title, address on the back (see ppt uploaded). The following disclosure needs to be included somewhere- Advisory services offered through Stonebrook Assets, LLC.
Updates

I uploaded a svg and ai file of the logo

Target Market(s)

Financial planning clients and financial advisors....so pretty diverse age range of about 40-70.

Industry/Entity Type

Financial Planning

Contact Information for Business Card

Tobias L. Fenwright, MBA
Founder/President
5287 E. Larkin Road
Suite 230
Omaha, NE 68190
Phone- (402) 555-0147
Cell- (402) 555-0183
Fax- (402) 555-0129
email- tobias@meridaleplan.example
web address- www.meridaleplan.example

Colors
1b1b1b
474747
d3d3d3
ffffff
9bcb3c
abd036

Requirements
Must have
• Must include logo provided, must be 2 sided, and must have disclosure...all of these items listed in project description

```html
<!DOCTYPE html>
<html lang="en">
<head>
<meta charset="utf-8">
<title>Meridale Circle — Business Card</title>
<link rel="stylesheet" href="https://fonts.googleapis.com/css2?family=Cinzel:wght@400;600&family=Arimo:wght@400&display=swap">
<style>
  :root {
    --ink: #1b1b1b;
    --graphite: #474747;
    --silver: #d3d3d3;
    --paper: #ffffff;
    --leaf: #9bcb3c;
    --lime: #abd036;
    --stage: #e9e9e6;
  }
  * { margin: 0; padding: 0; box-sizing: border-box; }
  html, body { width: 1200px; height: 880px; overflow: hidden; }
  body {
    background: var(--stage);
    font-family: "Arimo", Arial, sans-serif;
    color: var(--ink);
    position: relative;
  }
  .card {
    position: absolute;
    left: 280px;
    width: 640px;
    height: 366px;
    border-radius: 22px;
    overflow: hidden;
    box-shadow: 0 10px 28px rgba(0,0,0,.22);
  }

  /* Front side */
  .card-front { top: 52px; background: var(--graphite); }
  .front-photo {
    position: absolute; inset: 0;
    background: radial-gradient(ellipse at 60% 45%, #7a7a7a 0%, #555 45%, #333 100%);
  }
  .definition { position: absolute; inset: 0; }
  .definition-word {
    position: absolute; left: 150px; top: 112px;
    font-family: "Cinzel", "Times New Roman", serif;
    font-size: 60px; font-weight: 400; letter-spacing: 1px;
    color: var(--leaf);
  }
  .definition-sound {
    position: absolute; left: 330px; top: 188px;
    font-size: 17px; color: var(--paper); letter-spacing: .5px;
  }
  .definition-meaning {
    position: absolute; left: 58px; top: 262px;
    font-size: 18px; color: var(--paper); letter-spacing: .6px;
  }

  /* Back side */
  .card-back { top: 462px; background: var(--paper); }
  .brand {
    position: absolute; left: 0; right: 0; top: 58px;
    display: flex; justify-content: center; align-items: center; gap: 14px;
  }
  .brand-dot { width: 26px; height: 26px; border-radius: 50%; background: var(--leaf); }
  .brand-name {
    font-family: "Cinzel", "Times New Roman", serif;
    font-size: 42px; font-weight: 600; color: var(--ink); letter-spacing: 1px;
  }
  .name-band {
    position: absolute; left: 0; right: 0; top: 142px; height: 46px;
    background: var(--ink);
    display: flex; align-items: center; padding-left: 150px;
  }
  .person-name {
    font-family: "Cinzel", "Times New Roman", serif;
    font-size: 22px; color: var(--paper); letter-spacing: 1px;
  }
  .person-title {
    position: absolute; left: 190px; top: 194px;
    font-size: 17px; color: var(--leaf);
  }
  .contact-list {
    position: absolute; right: 332px; top: 224px;
    list-style: none; text-align: right;
    font-size: 16px; line-height: 21px; color: var(--ink);
  }
  .contact-list li { display: flex; justify-content: flex-end; align-items: center; gap: 8px; }
  .contact-list svg { width: 13px; height: 13px; fill: var(--leaf); flex: none; }
  .divider {
    position: absolute; left: 326px; top: 224px; width: 1px; height: 84px;
    background: var(--silver);
  }
  .address {
    position: absolute; left: 346px; top: 224px;
    font-style: normal; font-size: 16px; line-height: 21px; color: var(--ink);
  }
  .address .web-host { color: var(--leaf); }
  .foot-band {
    position: absolute; left: 0; right: 0; top: 322px; height: 26px;
    background: var(--ink);
    display: flex; align-items: center; justify-content: center;
  }
  .disclosure {
    font-size: 11px; letter-spacing: .4px; color: var(--silver);
  }
</style>
</head>
<body>

<section class="card card-front" aria-label="Card front">
  <div class="front-photo" role="img" aria-label="Grayscale photo of hands joining puzzle pieces"></div>
  <div class="definition">
    <div class="definition-word">MERIDALE</div>
    <div class="definition-sound">ˈmer·ə·dāl</div>
    <div class="definition-meaning">: to come together and unite in common interest and focus</div>
  </div>
</section>

<section class="card card-back" aria-label="Card back">
  <div class="brand">
    <span class="brand-dot"></span>
    <span class="brand-name">MERIDALE CIRCLE</span>
  </div>

  <div class="name-band">
    <span class="person-name">TOBIAS L. FENWRIGHT, MBA</span>
  </div>
  <div class="person-title">Founder/President</div>

  <ul class="contact-list">
    <li>(402) 555-0147
      <svg viewBox="0 0 16 16" aria-hidden="true"><path d="M3 1l3 3-1.5 2a9 9 0 0 0 5.5 5.5L12 10l3 3-2 2C7 15 1 9 1 3z"/></svg>
    </li>
    <li>(402) 555-0183
      <svg viewBox="0 0 16 16" aria-hidden="true"><path d="M4 0h8a1 1 0 0 1 1 1v14a1 1 0 0 1-1 1H4a1 1 0 0 1-1-1V1a1 1 0 0 1 1-1zm1 2v10h6V2z"/></svg>
    </li>
    <li>(402) 555-0129
      <svg viewBox="0 0 16 16" aria-hidden="true"><path d="M4 1h8v4H4zM1 6h14v7h-3v2H4v-2H1zm4 4v4h6v-4z"/></svg>
    </li>
    <li>tobias@meridaleplan.example
      <svg viewBox="0 0 16 16" aria-hidden="true"><path d="M1 3h14v10H1zm1 1l6 5 6-5z"/></svg>
    </li>
  </ul>

  <div class="divider"></div>

  <address class="address">
    5287 E. Larkin Road<br>
    Suite 230<br>
    Omaha, NE 68190<br>
    www.<span class="web-host">meridaleplan</span>.example
  </address>

  <div class="foot-band">
    <p class="disclosure">Advisory services offered through Stonebrook Assets, LLC</p>
  </div>
</section>

</body>
</html>
```